Simplified minimalist but bold website

Design a website for a brand 'Brighten Every Day' that shares ideas to make managing home and health easier through email swap series, webinars and eventually courses.

Simple landing page to attract users to sign up for a freebie.

Target Market(s)

women with families & homes to run

Number of Pages Required

1 page

Font styles to use
Sans Serif

Colors
e667a6
b768aa
acd136
ffffff
959595

Requirements
Must have
• Simplified look, line icons, opt-in template, contact us form

```html
<!DOCTYPE html>
<html lang="en">
<head>
<meta charset="utf-8">
<title>Brighten Every Day</title>
<link rel="stylesheet" href="https://fonts.googleapis.com/css2?family=Montserrat:wght@400;500;600;700;800&display=swap">
<style>
:root{
  --pink:#e667a6;
  --blue:#35a6d8;
  --pink-soft:#fcedf4;
  --blue-soft:#e8f5fb;
  --ink:#333333;
  --grey:#555555;
  --line:#d6d6d6;
  --footer:#4a4a4a;
  --white:#ffffff;
}
*{box-sizing:border-box;margin:0;padding:0}
html,body{width:764px;height:1200px;overflow:hidden}
body{position:relative;font-family:"Montserrat",Arial,sans-serif;color:var(--ink);background:var(--white)}
.abs{position:absolute}

/* hero */
.hero{left:0;top:0;width:764px;height:385px;overflow:hidden}
.hero-photo{left:0;top:0;width:764px;height:385px;
  background:linear-gradient(100deg,#8a7660 0%,#a08466 30%,#8d857c 55%,#b3aca5 75%,#9a948d 100%)}
.hero-panel{left:0;top:94px;width:362px;height:219px;border-radius:0 170px 170px 0/0 110px 110px 0;
  background:rgba(255,255,255,.18);border:1px solid rgba(255,255,255,.25);border-left:none}
.brand{left:0;top:8px;width:764px;text-align:center;font-weight:800;font-size:15px;color:var(--white);letter-spacing:.3px}
.brand-dot{display:inline-block;width:8px;height:8px;border-radius:50%;background:var(--pink);margin-right:7px;vertical-align:1px}
.hero-title{left:70px;top:147px;width:290px;font-weight:800;font-size:30px;line-height:33px;color:var(--white);text-shadow:0 1px 3px rgba(0,0,0,.25)}
.hero-sub{left:70px;top:223px;width:290px;font-size:14px;line-height:22px;color:var(--white)}
.hero-chevron{left:374px;top:354px}

/* offers */
.col{top:385px;width:382px;height:418px}
.col-left{left:0;background:var(--pink-soft)}
.col-right{left:382px;width:382px;background:var(--blue-soft)}
.divider{left:381px;top:385px;width:2px;height:418px;background:linear-gradient(var(--blue) 0 50%,var(--pink) 50% 100%)}
.col-inner{position:absolute;left:0;top:0;width:100%;text-align:center}
.kicker{position:absolute;left:0;top:31px;width:100%;font-size:13px;color:var(--grey)}
.offer-title{position:absolute;left:0;top:60px;width:100%;font-size:16.5px;font-weight:700;color:var(--pink)}
.offer-text{position:absolute;left:20px;top:93px;width:342px;font-size:8.8px;line-height:15px;font-weight:500;color:var(--ink)}
.offer-text p+p{margin-top:12px}
.btn{position:absolute;display:flex;align-items:center;justify-content:center;color:var(--white);font-size:9px;font-weight:500;border-radius:2px;letter-spacing:.2px}
.btn-pink{background:var(--pink)}
.btn-blue{background:var(--blue)}

.form-box{position:absolute;left:38px;top:253px;width:306px;height:129px;border:2px solid}
.form-box.pink{border-color:var(--pink)}
.form-box.blue{border-color:var(--blue)}
.form-legend{position:absolute;left:50%;top:-11px;transform:translateX(-50%);padding:0 10px;font-size:13px;color:var(--ink);white-space:nowrap}
.pink .form-legend{background:var(--pink-soft)}
.blue .form-legend{background:var(--blue-soft)}
.form-legend::before,.form-legend::after{content:"";position:absolute;top:7px;width:8px;height:8px;border-radius:50%}
.pink .form-legend::before,.pink .form-legend::after{background:var(--pink)}
.blue .form-legend::before,.blue .form-legend::after{background:var(--blue)}
.form-legend::before{left:-12px}
.form-legend::after{right:-12px}
.field{position:absolute;left:24px;width:254px;height:23px;background:var(--white);border:1px solid var(--line);font-size:9px;color:var(--grey);padding-left:6px;display:flex;align-items:center;text-align:left}

.circle{position:absolute;top:96px;width:122px;height:122px;border-radius:50%;color:var(--white);text-align:center}
.circle-steps{left:75px;background:radial-gradient(circle at 40% 40%,#e98abb,#d44f93)}
.circle-simple{left:185px;background:radial-gradient(circle at 40% 40%,#6cc3e6,#2f9fd0);opacity:.95}
.circle h3{margin-top:33px;font-size:14.5px;font-weight:700}
.circle .bar{width:17px;height:2px;background:var(--white);margin:6px auto 10px}
.circle p{font-size:11px;line-height:16px}

/* detail */
.detail-title{left:0;top:846px;width:764px;text-align:center;font-size:19px;font-weight:700;color:var(--pink)}
.detail-rule{left:362px;top:883px;width:40px;height:2px;background:var(--pink)}
.detail-text{left:80px;top:909px;width:604px;text-align:center;font-size:9px;line-height:17px;color:var(--ink)}
.detail-note{left:178px;top:965px;width:409px;height:48px;background:var(--pink);color:var(--white);font-size:10.5px;line-height:17px;text-align:center;display:flex;align-items:center;justify-content:center;padding:0 6px;border-radius:2px}
.detail-invite{left:100px;top:1039px;width:564px;text-align:center;font-size:10.5px;line-height:17px;font-weight:700;color:var(--blue)}

.footer{left:0;top:1163px;width:764px;height:37px;background:var(--footer);color:var(--white);font-size:9.5px;display:flex;align-items:center;justify-content:center;font-weight:500}
</style>
</head>
<body>

<header class="abs hero">
  <div class="abs hero-photo" role="img" aria-label="Photo of a woman working on a laptop in a bright home with wooden floor"></div>
  <div class="abs hero-panel"></div>
  <div class="abs brand"><span class="brand-dot"></span>Brighten Every Day</div>
  <h1 class="abs hero-title">BRIGHTEN EVERY DAY</h1>
  <p class="abs hero-sub">Chances are life is a little overwhelming.<br>Let us help</p>
  <svg class="abs hero-chevron" width="16" height="14" viewBox="0 0 16 14" aria-hidden="true">
    <polyline points="2,2 8,7 14,2" fill="none" stroke="#fff" stroke-width="1.6"/>
    <polyline points="2,7 8,12 14,7" fill="none" stroke="#fff" stroke-width="1.6"/>
  </svg>
</header>

<section class="abs col col-left">
  <div class="col-inner">
    <p class="kicker">Baby Steps... (try out a few of our tricks)</p>
    <h2 class="offer-title">Swaps Email Series</h2>
    <div class="offer-text">
      <p>Save TIME, MONEY and SANITY with simple product swaps.</p>
      <p>Reduce the amount of work it takes to run your home. Swap out existing products for more sustainable ones. Each swap saves you work, clutter, time &amp; money.</p>
    </div>
    <a class="btn btn-pink" style="left:100px;top:188px;width:100px;height:27px">SEE SAMPLE SWAP</a>
    <a class="btn btn-blue" style="left:210px;top:188px;width:72px;height:27px">LEARN MORE</a>
    <form class="form-box pink">
      <span class="form-legend">Send your ideas my way...</span>
      <div class="field" style="top:23px">Name</div>
      <div class="field" style="top:51px">Email</div>
      <span class="btn btn-pink" style="left:96px;top:83px;width:110px;height:27px">SEND ME THE GUIDE!</span>
    </form>
  </div>
</section>

<section class="abs col col-right">
  <div class="col-inner">
    <p class="kicker">Big Leap... (I'm ready to roll up my sleeves)</p>
    <h2 class="offer-title">Decluttering Guide</h2>
    <div class="circle circle-steps" role="img" aria-label="Pink-toned photo of planning notes"><h3>STEPS</h3><div class="bar"></div><p>Let Us Help!</p></div>
    <div class="circle circle-simple" role="img" aria-label="Blue-toned photo of a tidy home"><h3>SIMPLE</h3><div class="bar"></div><p>Chances<br>Let Us Help!</p></div>
    <form class="form-box blue">
      <span class="form-legend">Sign Up With Us...</span>
      <div class="field" style="top:23px">Name</div>
      <div class="field" style="top:51px">Email</div>
      <span class="btn btn-blue" style="left:96px;top:83px;width:110px;height:27px">SIGN ME UP!</span>
    </form>
  </div>
</section>
<div class="abs divider"></div>

<section>
  <h2 class="abs detail-title">Swaps Email Series</h2>
  <div class="abs detail-rule"></div>
  <p class="abs detail-text">Save TIME, MONEY and SANITY with simple product swaps. And reduce the amount of work it takes to run your home. Swap out existing products for more sustainable ones. Each swap save you work, clutter, time &amp; money.</p>
  <p class="abs detail-note">You get an email 2x weekly for 6-12 weeks only Get even more if you feel they are helpful to you.</p>
  <p class="abs detail-invite">Join our monthly SIMPLE SWAP SHARING web jams with other mums and get even more ideas.<br>Better yet, come with great tips of your own to share.</p>
  <a class="btn btn-blue" style="left:327px;top:1092px;width:110px;height:27px;font-size:10px">SIGN ME UP!</a>
</section>

<footer class="abs footer">Copyrights @ 2018 Brighten Every Day. All Rights Reserved.</footer>

</body>
</html>
```